Feminine colorfull packaging for coconut skin care brand

We need a design that can be used on different types of packaging for beauty products likes creams, oils, etc.
The products that we will launch will be made with one key ingredient of coconut oil + other added ingredients depending on the type of product. The entire marketing will therefore be based on COCONUTS, palmtrees, sand, beach, bronzing on the beach, holiday feeling, nature, femininity, etc. = A Lifestyle brand with a tropical vibe.
Packaging can be a pot for creams, flaskes for lotions, smaller bottles for oils, etc. Mostly the standard packaging used for beauty products.
We would like to use the color pink ( this can be bright or pastel or any tone of pink) to address the feminine side of our product and a tone of blue-green ( pastel, bright or any tone of this color) to accentuate the use of coconut.
Third would be the color white (this can be added through an accent somewhere on the packaging or this can be the brand name that is written in white)
Lastely we would like the packaging to be light, fresh and playfull. Please feel free to use different colors or shapes ( we do not yet have a logo. This can then be designed followed on the packaging)
The design will be printed on plastic packaging. We are open to very creative designs. We are looking for packaging that catches the eye by its design and/or colors, that is different than others, that distinguishes the product because of its packaging design.
Updates
Low design quality
Target Market(s)
Women between 20 - 35 years
Industry/Entity Type
Beauty
Colors
Look and feel

```html
<!DOCTYPE html>
<html lang="en">
<head>
<meta charset="utf-8">
<title>Lumara Body Lotion Label</title>
<link rel="stylesheet" href="https://fonts.googleapis.com/css2?family=Montserrat:wght@400;500&display=swap">
<style>
  :root {
    --page: #f3f1ee;
    --lid-pink: #f6d9dc;
    --lid-shade: #efcdd2;
    --label-teal: #8cc3ae;
    --leaf-pink: #f7dbdc;
    --white: #ffffff;
  }
  html, body {
    margin: 0;
    padding: 0;
    width: 1200px;
    height: 900px;
    overflow: hidden;
    background: var(--page);
  }
  .canvas {
    position: relative;
    width: 1200px;
    height: 900px;
    display: flex;
    flex-direction: column;
    align-items: center;
    justify-content: center;
  }
  .lid-band {
    width: 640px;
    height: 190px;
    background: linear-gradient(180deg, var(--lid-pink) 0%, var(--lid-shade) 100%);
    border-radius: 26px 26px 10px 10px;
  }
  .label {
    position: relative;
    width: 640px;
    height: 390px;
    margin-top: 8px;
    background: var(--label-teal);
    border-radius: 8px 8px 30px 30px;
    overflow: hidden;
    display: flex;
    flex-direction: column;
    align-items: center;
    font-family: "Montserrat", sans-serif;
    color: var(--white);
  }
  .leaf {
    position: absolute;
    background: var(--leaf-pink);
    border-radius: 50%;
  }
  .leaf--top-left { width: 130px; height: 160px; left: -30px; top: 14px; transform: rotate(-20deg); }
  .leaf--bottom-left { width: 130px; height: 115px; left: 30px; top: 268px; transform: rotate(30deg); }
  .leaf--right { width: 110px; height: 170px; right: -40px; top: 110px; transform: rotate(15deg); }
  .brand-name {
    margin: 82px 0 0;
    font-size: 58px;
    font-weight: 500;
    letter-spacing: 1px;
    line-height: 1;
  }
  .product-lines {
    margin: 52px 0 0;
    font-size: 30px;
    font-weight: 400;
    letter-spacing: 1.5px;
    line-height: 1.25;
    text-align: center;
  }
</style>
</head>
<body>
  <main class="canvas">
    <div class="lid-band"></div>
    <section class="label">
      <div class="leaf leaf--top-left" role="img" aria-label="Pale pink monstera leaf illustration"></div>
      <div class="leaf leaf--bottom-left" role="img" aria-label="Pale pink monstera leaf illustration"></div>
      <div class="leaf leaf--right" role="img" aria-label="Pale pink monstera leaf illustration"></div>
      <h1 class="brand-name">Lumara</h1>
      <p class="product-lines">body lotion<br>coconut extracts</p>
    </section>
  </main>
</body>
</html>
```